BQR, LLC Original

I need a business card design for a new company in Gaithersburg, MD. Though the name of the company is Wiremasters Of Northfield (BQR) we specialize in commercial kitchen ventilation systems as a complete turnkey project or as a service provider. We can design the entire system including the hoods, fans, ductwork, and fire system. We also specialize in fire alarm service, design, install and inspection. We are experts on any Ventaro Dynamics equipment including Pulsar VXM, Pulsar Canopies, EMS controls, Standard controls, PCU filtration and Make-up Air units with heaters and cooling. We can repair/retrofit old water wash hood systems as well. We are experts with local code requirements and upgrades.

Industry/Entity Type

Business

Contact Information for Business Card

Dale Pruitt, Wiremasters Of Northfield, LLC; 240-555-0187 Cell, Larkmoor, MD 20999. Dalep@wiremastersnorthfield.example

```html
<!DOCTYPE html>
<html lang="en">
<head>
<meta charset="utf-8">
<title>Wiremasters Of Northfield, LLC — Business Card</title>
<link rel="stylesheet" href="https://fonts.googleapis.com/css2?family=Arimo:wght@400;700&display=swap">
<style>
  :root {
    --bg: #d9d6d2;
    --card: #050505;
    --brand-blue: #1f8fe0;
    --ring-blue: #2f55b8;
    --accent-orange: #f29a12;
    --band-light: #3fb0f0;
    --band-dark: #0b5ea6;
  }
  * { margin: 0; padding: 0; box-sizing: border-box; }
  html, body { width: 1200px; height: 960px; overflow: hidden; }
  body {
    background: var(--bg);
    font-family: "Arimo", Arial, sans-serif;
    position: relative;
  }
  .card {
    position: absolute;
    top: 148px;
    width: 380px;
    height: 664px;
    background: var(--card);
    box-shadow: 0 14px 30px rgba(0,0,0,0.35);
    overflow: hidden;
  }
  .card--front { left: 170px; }
  .card--back { left: 650px; }

  .brand {
    position: absolute;
    left: 0; right: 0;
    display: flex;
    align-items: center;
    justify-content: center;
    gap: 12px;
  }
  .card--front .brand { top: 250px; }
  .card--back .brand { top: 120px; }
  .brand__mark {
    width: 34px; height: 34px;
    border-radius: 50%;
    border: 3px solid var(--ring-blue);
    flex: none;
  }
  .brand__name {
    color: var(--brand-blue);
    font-size: 17px;
    font-weight: 400;
    letter-spacing: 0.04em;
    line-height: 1.25;
    white-space: nowrap;
  }

  .person {
    position: absolute;
    top: 230px;
    left: 0; right: 0;
    text-align: center;
    color: var(--accent-orange);
  }
  .person__name { font-size: 30px; font-weight: 700; }
  .person__role { font-size: 17px; font-weight: 400; margin-top: 4px; }

  .contact {
    position: absolute;
    top: 350px;
    left: 0; right: 0;
    list-style: none;
    text-align: center;
    color: var(--accent-orange);
    font-size: 17px;
    line-height: 1.5;
  }

  .band {
    position: absolute;
    left: 0; right: 0; bottom: 0;
    height: 118px;
    border-top: 3px solid var(--band-light);
    background: linear-gradient(180deg, var(--band-light) 0%, #1d86d2 45%, var(--band-dark) 100%);
    box-shadow: inset 0 8px 0 var(--card);
  }
</style>
</head>
<body>
  <section class="card card--front" aria-label="Card front">
    <div class="brand">
      <span class="brand__mark" aria-hidden="true"></span>
      <span class="brand__name">Wiremasters Of Northfield, LLC</span>
    </div>
  </section>

  <section class="card card--back" aria-label="Card back">
    <div class="brand">
      <span class="brand__mark" aria-hidden="true"></span>
      <span class="brand__name">Wiremasters Of Northfield, LLC</span>
    </div>
    <div class="person">
      <p class="person__name">Dale Pruitt</p>
      <p class="person__role">Electricians</p>
    </div>
    <ul class="contact">
      <li>240-555-0187</li>
      <li>Dalep@wiremastersnorthfield.example</li>
      <li>Larkmoor, MD 20999</li>
    </ul>
    <div class="band" aria-hidden="true"></div>
  </section>
</body>
</html>
```